Automotive component supplier needs a business card design

We need a business card design for our company called Velran Global Components Ltd based in the UK. We are a supplier of interior and exterior components to premium car manufacturers such as Corvel Ashby, Hadley Fenn, Marquist and Tavarelli. We would like to see a modern business card design that uses the colour blue.

Target Market(s)

Premium automotive car manufacturers.

Industry/Entity Type

Automotive

Contact Information for Business Card

Company Name : Velran Global Components Limited
Address: 17 Marlow Yard, Upper Heath, Warwick, CV31 8QL, United Kingdom
Web Address : www.velrancomponents-example.co.uk

Font styles to use
Other font styles liked:
• Helvetica

Colors
3176b5
0255a3
85acd3
cfdeed
cee9f5
85cae6
34a6d7
0692cd
9bcb3c

Requirements
Must have
• Clear company logo and a mixture of blue colours.
Nice to have
• A high quality modern image.
Should not have
• Multiple colours.

```html
<!DOCTYPE html>
<html lang="en">
<head>
<meta charset="utf-8">
<title>Velran Global Components – Business Card</title>
<link rel="stylesheet" href="https://fonts.googleapis.com/css2?family=Arimo:wght@400&family=Michroma&display=swap">
<style>
  :root {
    --blue: #0692cd;
    --brand-blue: #0a84c6;
    --green: #9bcb3c;
    --white: #ffffff;
    --backdrop: #e9edf1;
    --shadow: rgba(0, 0, 0, 0.25);
  }
  * { margin: 0; padding: 0; box-sizing: border-box; }
  html, body { width: 1200px; height: 843px; overflow: hidden; }
  body { background: var(--backdrop); position: relative; font-family: "Arimo", Helvetica, Arial, sans-serif; }

  .card {
    position: absolute;
    top: 252px;
    width: 559px;
    height: 319px;
    border-radius: 14px;
    overflow: hidden;
    box-shadow: 0 4px 10px var(--shadow);
  }
  .card--front { left: 28px; background: var(--white); }
  .card--back { left: 614px; background: var(--blue); }
  .card__shape { position: absolute; inset: 0; width: 100%; height: 100%; }

  .brand {
    position: absolute;
    display: flex;
    align-items: center;
    gap: 10px;
    font-family: "Michroma", "Arial Black", sans-serif;
    font-size: 15px;
    line-height: 1.45;
    letter-spacing: 0.5px;
    color: var(--brand-blue);
    text-transform: uppercase;
  }
  .brand__mark { width: 14px; height: 14px; background: var(--green); flex: none; }
  .card--front .brand { left: 24px; top: 134px; }
  .card--back .brand { left: 30px; top: 134px; }

  .contact {
    position: absolute;
    right: 24px;
    top: 84px;
    text-align: right;
    color: var(--white);
    font-size: 12.5px;
    line-height: 17px;
    white-space: nowrap;
  }
  .contact__name {
    font-family: "Michroma", "Arial Black", sans-serif;
    font-size: 15px;
    letter-spacing: 0.8px;
    line-height: 20px;
  }
  .contact__role { color: var(--green); font-size: 12.5px; margin-bottom: 4px; }
  .contact__address { margin-bottom: 7px; }
  .contact__line { display: flex; justify-content: flex-end; align-items: center; gap: 7px; }
  .contact__icon { width: 9px; height: 9px; flex: none; }

  .card__web {
    position: absolute;
    right: 30px;
    bottom: 17px;
    color: var(--white);
    font-size: 12.5px;
  }
</style>
</head>
<body>

<section class="card card--front">
  <svg class="card__shape" viewBox="0 0 559 319" aria-hidden="true">
    <circle cx="470" cy="160" r="210" fill="var(--blue)"/>
    <path d="M338 6 A180 180 0 0 0 338 313 A184.7 184.7 0 0 1 338 6 Z" fill="var(--blue)"/>
  </svg>

  <div class="brand">
    <span class="brand__mark"></span>
    <span class="brand__name">Velran Global<br>Components</span>
  </div>

  <div class="contact">
    <p class="contact__name">DORIAN WELLES</p>
    <p class="contact__role">Director</p>
    <p class="contact__address">17 Marlow Yard, Upper Heath<br>Warwick, CV31 8QL, UK</p>
    <p class="contact__line">780 555-0142
      <svg class="contact__icon" viewBox="0 0 10 10"><path d="M2 0.5 L3.8 2.6 L2.9 4 Q4.3 6.3 6 7.1 L7.4 6.2 L9.5 8 L8 9.6 Q2.5 8.5 0.4 2 Z" fill="var(--green)"/></svg>
    </p>
    <p class="contact__line">780 555-0187
      <svg class="contact__icon" viewBox="0 0 10 10"><rect x="2.5" y="0.5" width="5" height="9" rx="1" fill="none" stroke="var(--green)" stroke-width="1.2"/></svg>
    </p>
    <p class="contact__line">contact@velran-example.co.uk
      <svg class="contact__icon" viewBox="0 0 10 10"><rect x="0.5" y="2" width="9" height="6" fill="var(--green)"/><path d="M0.5 2 L5 5.5 L9.5 2" fill="none" stroke="var(--blue)" stroke-width="0.9"/></svg>
    </p>
    <p class="contact__line">www.velrancomponents-example.co.uk
      <svg class="contact__icon" viewBox="0 0 10 10"><circle cx="5" cy="5" r="4.3" fill="none" stroke="var(--green)" stroke-width="1"/><path d="M0.7 5 H9.3 M5 0.7 Q2.5 5 5 9.3 M5 0.7 Q7.5 5 5 9.3" fill="none" stroke="var(--green)" stroke-width="0.8"/></svg>
    </p>
  </div>
</section>

<section class="card card--back">
  <svg class="card__shape" viewBox="0 0 559 319" aria-hidden="true">
    <rect x="0" y="0" width="90" height="319" fill="var(--green)"/>
    <circle cx="86" cy="160" r="194" fill="var(--green)"/>
    <path d="M208 0 A198 198 0 0 1 208 319 L202 319 A194 194 0 0 0 202 0 Z" fill="var(--blue)"/>
    <path d="M214 8 A206 206 0 0 1 214 311 A200 200 0 0 0 214 8 Z" fill="var(--green)"/>
  </svg>

  <div class="brand">
    <span class="brand__mark"></span>
    <span class="brand__name">Velran Global<br>Components</span>
  </div>

  <p class="card__web">www.velrancomponents-example.co.uk</p>
</section>

</body>
</html>
```